Business card for a new cabinet shop company named Veloran Cabinets for high end cabinets

Design a business card, thinking dark rich green with colours to speak of high end luxury ie; cream, gold, black possibly

Mitchell Tarrowby
Director Craftsman
Email: info@veloranjoinery-example.com.au
Instagram : @veloran.cabinets

```html
<!DOCTYPE html>
<html lang="en">
<head>
<meta charset="utf-8">
<title>Veloran Cabinets – Business Card</title>
<link rel="stylesheet" href="https://fonts.googleapis.com/css2?family=Jost:wght@400;500;700&display=swap">
<style>
  :root {
    --backdrop: #2e302f;
    --card: #0f2a21;
    --card-soft: #18392d;
    --card-deep: #0a1f18;
    --gold: #c9a95f;
    --cream: #efe6d2;
  }
  * { margin: 0; padding: 0; box-sizing: border-box; }
  html, body {
    width: 1200px; height: 694px; overflow: hidden;
    background: var(--backdrop);
    font-family: "Jost", sans-serif;
  }
  .canvas {
    position: relative; width: 1200px; height: 694px;
    display: flex; align-items: center; justify-content: center; gap: 40px;
  }
  .card {
    position: relative; width: 540px; height: 330px;
    background: var(--card); border-radius: 18px; overflow: hidden;
  }

  /* Front */
  .card-front .pattern-area {
    position: absolute; inset: 0;
    background: radial-gradient(ellipse at 30% 60%, var(--card-soft) 0%, var(--card) 55%, var(--card-deep) 100%);
  }
  .lockup {
    position: absolute; display: flex; align-items: center; gap: 14px;
    color: var(--gold); font-weight: 500; white-space: nowrap;
  }
  .lockup-mark {
    border: 2px solid var(--gold); border-radius: 50%;
    flex: none;
  }
  .card-front .lockup { left: 50%; top: 50%; transform: translate(-50%, -50%); font-size: 44px; }
  .card-front .lockup-mark { width: 44px; height: 44px; }

  /* Back */
  .card-back {
    background: linear-gradient(135deg, var(--card) 0%, var(--card-deep) 100%);
  }
  .card-back .decoration-area {
    position: absolute; right: 30px; top: 30px; width: 190px; height: 210px;
    border-radius: 14px;
    background: radial-gradient(circle at 50% 45%, var(--card-soft) 0%, transparent 75%);
  }
  .card-back .lockup { left: 40px; top: 44px; font-size: 30px; }
  .card-back .lockup-mark { width: 30px; height: 30px; }
  .identity {
    position: absolute; left: 40px; top: 150px;
    padding-left: 16px; border-left: 5px solid var(--gold);
  }
  .person-name { color: var(--gold); font-weight: 700; font-size: 28px; line-height: 1.1; }
  .person-title { color: var(--cream); font-weight: 400; font-size: 15px; margin-top: 4px; }
  .contact-list {
    position: absolute; left: 61px; top: 232px; list-style: none;
    color: var(--cream); font-size: 14px;
  }
  .contact-item { display: flex; align-items: center; gap: 10px; height: 24px; }
  .contact-icon { width: 14px; height: 14px; flex: none; color: var(--gold); }
  .plain-square { width: 13px; height: 13px; border: 1.6px solid var(--gold); border-radius: 3px; flex: none; }
  .gold-rule {
    position: absolute; left: 0; right: 0; bottom: 0; height: 6px; background: var(--gold);
  }
</style>
</head>
<body>
<main class="canvas">

  <section class="card card-front" aria-label="Business card front">
    <div class="pattern-area" role="img" aria-label="Faint embossed repeating brand pattern across the card"></div>
    <div class="lockup">
      <span class="lockup-mark"></span>
      <span class="lockup-name">Veloran Cabinets</span>
    </div>
  </section>

  <section class="card card-back" aria-label="Business card back">
    <div class="decoration-area" role="img" aria-label="Large embossed brand decoration in glossy deep green"></div>

    <div class="lockup">
      <span class="lockup-mark"></span>
      <span class="lockup-name">Veloran Cabinets</span>
    </div>

    <div class="identity">
      <p class="person-name">Mitchell Tarrowby</p>
      <p class="person-title">Director Craftsman</p>
    </div>

    <ul class="contact-list">
      <li class="contact-item">
        <svg class="contact-icon" viewBox="0 0 16 16" aria-hidden="true">
          <rect x="1" y="3" width="14" height="10" rx="1" fill="none" stroke="currentColor" stroke-width="1.6"/>
          <path d="M1.5 3.5 L8 9 L14.5 3.5" fill="none" stroke="currentColor" stroke-width="1.6"/>
        </svg>
        <span>info@veloranjoinery-example.com.au</span>
      </li>
      <li class="contact-item">
        <svg class="contact-icon" viewBox="0 0 16 16" aria-hidden="true">
          <circle cx="8" cy="8" r="6.5" fill="none" stroke="currentColor" stroke-width="1.6"/>
        </svg>
        <span>veloranjoinery-example.com.au</span>
      </li>
      <li class="contact-item">
        <span class="plain-square" aria-hidden="true"></span>
        <span>@veloran.cabinets</span>
      </li>
    </ul>

    <div class="gold-rule"></div>
  </section>

</main>
</body>
</html>
```